We need a new business card that reflects who we are. Professional, classy, modern, and service ori

We need a business card design for a window coverings design company in Kansas City called Bright Lane Interiors. We offer professional, modern, and high quality window covering products. We are looking to portray an image of a big, national franchise. We are a 5 location (with showrooms) business with 10 professional designers and 4 professional installers. These cards will be used with Thank you cards, given to realtors, and asked for referrals with.

Target Market(s)

Kansas City

Industry/Entity Type

Business

Contact Information for Business Card

We would like our card to look clean and simple on the front, featuring our logo and Marlow Fenwick's. Our designers' phone numbers and emails should be displayed as well as their title.

Font styles to use
Sans Serif

Colors

Designer to choose colors to be used in the design.

Requirements
Must have
• Front - Logos, name, phone number, email address
• Back - Showroom locations, social media? Appt date/time?
Nice to have
• I would like a clean and modern look (not contemporary. I like a white background, but I am open to ideas. Looking for a "National chain" look for a small business.
Should not have
• Too much busyness.

```html
<!DOCTYPE html>
<html lang="en">
<head>
<meta charset="utf-8">
<title>Bright Lane Interiors – Business Card</title>
<link href="https://fonts.googleapis.com/css2?family=Marcellus&family=Sorts+Mill+Goudy&family=Roboto:wght@400;500&family=Roboto+Condensed:wght@500&display=swap" rel="stylesheet">
<style>
  :root{
    --backdrop:#2b2b2b;
    --card:#f4f4f4;
    --brand-red:#c8373d;
    --ink:#111111;
    --text-grey:#4a4a4a;
    --partner-grey:#59626b;
    --partner-accent:#e88a2e;
    --rule-grey:#555555;
  }
  *{margin:0;padding:0;box-sizing:border-box}
  html,body{width:1200px;height:960px;overflow:hidden}
  body{background:var(--backdrop);position:relative;font-family:"Roboto",Arial,sans-serif}

  .card{position:absolute;width:600px;height:343px;background:var(--card)}
  .card--front{left:314px;top:113px}
  .card--back{left:311px;top:472px}

  /* front */
  .front-frame{position:absolute;inset:10px;border:1px solid var(--brand-red)}
  .brand{position:absolute;left:0;right:0;top:222px;display:flex;justify-content:center;align-items:center;gap:14px}
  .brand-square{width:26px;height:26px;background:var(--brand-red)}
  .brand-name{font-family:"Marcellus",Georgia,serif;font-size:40px;color:var(--ink);letter-spacing:.5px;line-height:1}
  .tagline{position:absolute;left:0;right:0;top:268px;text-align:center;font-family:"Sorts Mill Goudy",Georgia,serif;font-size:22px;color:var(--ink)}

  /* back */
  .designer-name{position:absolute;left:46px;top:46px;font-family:"Roboto Condensed",Arial,sans-serif;font-weight:500;font-size:24px;color:var(--brand-red);line-height:1}
  .designer-title{position:absolute;left:46px;top:72px;font-weight:500;font-size:15px;color:var(--ink)}
  .contact-list{position:absolute;left:47px;top:104px;list-style:none}
  .contact-list li{display:flex;align-items:center;gap:9px;height:19px;font-size:14.5px;color:var(--text-grey)}
  .contact-list svg{width:13px;height:13px;fill:var(--brand-red)}
  .social-row{position:absolute;left:47px;top:174px;display:flex;gap:3px}
  .social-dot{width:18px;height:18px;border-radius:50%;background:var(--brand-red)}
  .dotted{position:absolute;border-bottom:1px dotted var(--brand-red)}
  .dotted--social{left:133px;width:408px;top:188px}

  .showrooms{position:absolute;left:368px;top:46px}
  .showrooms h2{font-weight:500;font-size:14px;color:var(--brand-red);letter-spacing:.3px;line-height:18px}
  .showrooms ul{list-style:none}
  .showrooms li{font-size:14.5px;font-weight:500;color:var(--text-grey);line-height:18px;letter-spacing:.2px}
  .partner{position:absolute;left:368px;top:160px;display:flex;align-items:center;gap:5px}
  .partner-name{font-weight:500;font-size:12px;color:var(--partner-grey)}
  .partner-dot{width:14px;height:14px;border-radius:50%;background:var(--partner-accent)}

  .field-label{position:absolute;font-size:16px;color:var(--brand-red)}
  .label-name{left:43px;top:238px}
  .label-date{left:43px;top:279px;font-weight:500}
  .label-time{left:307px;top:279px;font-weight:500}
  .dotted--name{left:106px;width:432px;top:252px;border-color:var(--rule-grey)}
  .dotted--date{left:92px;width:213px;top:294px;border-color:var(--rule-grey)}
  .dotted--time{left:358px;width:135px;top:294px;border-color:var(--rule-grey)}
  .ampm{position:absolute;left:498px;top:283px;font-size:12.5px;color:var(--brand-red)}
</style>
</head>
<body>

<section class="card card--front">
  <div class="front-frame"></div>
  <div class="brand">
    <span class="brand-square"></span>
    <span class="brand-name">Bright Lane Interiors</span>
  </div>
  <p class="tagline">Blinds, Shades, Shutters, Draperies &amp; Decor</p>
</section>

<section class="card card--back">
  <h1 class="designer-name">DANIEL REEVES</h1>
  <p class="designer-title">DESIGNER</p>
  <ul class="contact-list">
    <li><svg viewBox="0 0 24 24"><path d="M6.6 10.8a15 15 0 0 0 6.6 6.6l2.2-2.2c.3-.3.7-.4 1-.2 1.1.4 2.3.6 3.6.6.6 0 1 .4 1 1V20c0 .6-.4 1-1 1A17 17 0 0 1 3 4c0-.6.4-1 1-1h3.5c.6 0 1 .4 1 1 0 1.3.2 2.5.6 3.6.1.3 0 .7-.2 1z"/></svg>913.555.0148</li>
    <li><svg viewBox="0 0 24 24"><path d="M2 5h20v14H2z M4 7v.5l8 5 8-5V7l-8 5z" fill-rule="evenodd"/></svg>info@brightlaneinteriors.com</li>
    <li><svg viewBox="0 0 24 24"><circle cx="12" cy="12" r="10"/></svg>brightlaneinteriors.com</li>
  </ul>
  <div class="social-row">
    <span class="social-dot"></span><span class="social-dot"></span><span class="social-dot"></span><span class="social-dot"></span>
  </div>
  <div class="dotted dotted--social"></div>

  <div class="showrooms">
    <h2>SHOWROOM LOCATIONS</h2>
    <ul>
      <li>MAPLE RIDGE</li>
      <li>CEDAR HEIGHTS</li>
      <li>ASHFORD PARK</li>
      <li>WILLOW BEND</li>
      <li>STONE HARBOR</li>
    </ul>
  </div>
  <div class="partner">
    <span class="partner-name">Marlow Fenwick Gallery</span>
    <span class="partner-dot"></span>
  </div>

  <span class="field-label label-name">Name :</span>
  <div class="dotted dotted--name"></div>
  <span class="field-label label-date">Date :</span>
  <div class="dotted dotted--date"></div>
  <span class="field-label label-time">Time :</span>
  <div class="dotted dotted--time"></div>
  <span class="ampm">AM/PM</span>
</section>

</body>
</html>
```